Luxury Wine Label for New Startup Winery

We need a wine label for our new winery startup. We have worked with a local designer but do not feel the resulting label / logo have the elevation required to present our brand as a luxury wine. Our winery is called "Quailbrook Vineyards" and we are focused on extremely high quality hand crafted artisan and estate wines from the Pacific Northwest.
We would like to see designs that utilize a tree line, or other imagery that represents the "Quailbrook" part of our company name. Another interesting feature could be wood grain.
A logo will be required based on your design so please design with this in mind:
This logo should be consistent with the wine bottle label design, and should be representative of our high end exclusive wine while giving a sense of place (Oregon/ Pacific Northwest.)
I will supply an image of the design we received from our local designer, PLEASE NOTE: in general we do like wood grain and tree line concepts but feel the execution was poorly done.
ATTN: Logo design should be suitable for use on: Bottles (Red wine/rose/white wine), Bussiness cards, vehicle signage, business signage, etc
P.S.:
If you have a design that is not outside the box we are still interested in seeing it.
Label is for a burgundy style bottle with a label height of 3.5 - 4" and a width of 3.5-4"
any label <= 4"x4" and >=3.5"x3.5" will be acceptable:
HOWEVER Width should be greater than or equal to height due to the bottle format
Target Market(s)
Wine enthusiasts with adequate discretionary budgets to afford $100 bottles of wine.
Industry/Entity Type
Wine / Winery
Requirements
Must have
- A sense of luxury, a feel of exclusivity, and a theme consistent with our product and brand name
Nice to have
- Tree line, wood grain or other wood themes. Serif fonts
Should not have
- anything cheesy, off topic, hard to read script fonts or anything that makes the label hard to read from a few feet away or too busy

```html
<!DOCTYPE html>
<html lang="en">
<head>
<meta charset="utf-8">
<title>Quailbrook Vineyards – Label Presentation</title>
<link rel="stylesheet" href="https://fonts.googleapis.com/css2?family=Cinzel:wght@400;500&display=swap">
<style>
  :root {
    --board-white: #ffffff;
    --panel-grey: #c6c5c7;
    --rule-grey: #c8c8c8;
    --ink: #111111;
    --gold: #7c6b3a;
    --red-word: #c1272d;
    --rose-word: #e8676b;
    --white-word: #1a1a1a;
    --bottle-red-top: #3a3a3a;
    --bottle-red-bottom: #0d0d0d;
    --bottle-rose-top: #f08a6a;
    --bottle-rose-bottom: #e23a36;
  }
  * { box-sizing: border-box; margin: 0; padding: 0; }
  html, body { width: 1200px; height: 848px; overflow: hidden; background: var(--board-white); }
  .board { position: relative; width: 1200px; height: 848px; font-family: "Cinzel", serif; }
  .defs { position: absolute; width: 0; height: 0; }

  .identity { position: absolute; left: 0; top: 0; width: 731px; height: 848px; background: var(--board-white); }
  .wordmark { position: absolute; left: 110px; top: 78px; display: flex; align-items: center; gap: 86px; }
  .wordmark-dot { width: 70px; height: 70px; border-radius: 50%; background: var(--gold); flex: none; }
  .wordmark-name { color: var(--ink); font-weight: 400; font-size: 62px; line-height: 0.98; letter-spacing: 0.02em; margin-left: -15px; }
  .wordmark-name span { display: block; }
  .divider { position: absolute; left: 44px; top: 279px; width: 687px; height: 2px; background: var(--rule-grey); }

  .bottle { position: absolute; border-radius: 40px 40px 18px 18px; }
  .bottle-red { left: 130px; top: 318px; width: 137px; height: 499px; background: linear-gradient(var(--bottle-red-top), var(--bottle-red-bottom)); }
  .bottle-rose { left: 320px; top: 327px; width: 141px; height: 487px; background: linear-gradient(var(--bottle-rose-top), var(--bottle-rose-bottom)); }
  .bottle-white { left: 507px; top: 327px; width: 140px; height: 487px; background: linear-gradient(var(--bottle-rose-top), var(--bottle-rose-bottom)); }
  .bottle .label { position: absolute; left: 7px; top: 292px; font-size: 9.1px; }
  .bottle-rose .label, .bottle-white .label { top: 283px; left: 6px; }

  .label-panel { position: absolute; left: 731px; top: 0; width: 469px; height: 848px; background: var(--panel-grey); }
  .label-panel .label { position: absolute; left: 123px; font-size: 16px; }
  .label-panel .label-red { top: 49px; }
  .label-panel .label-rose { top: 320px; }
  .label-panel .label-white { top: 590px; left: 126px; }

  .label { position: relative; width: 13.9em; height: 13.9em; overflow: hidden; }
  .label-art { position: absolute; inset: 0; width: 100%; height: 100%; display: block; }
  .label-lockup { position: absolute; left: 2em; top: 1.1em; display: flex; align-items: center; gap: 0.75em; }
  .label-lockup-dot { width: 1.6em; height: 1.6em; border-radius: 50%; background: var(--gold); flex: none; }
  .label-lockup-name { color: var(--gold); font-size: 1.12em; line-height: 1; letter-spacing: 0.02em; }
  .label-lockup-name span { display: block; }
  .label-variety { position: absolute; left: 0; right: 0; top: 5.7em; text-align: center; font-size: 1.15em; line-height: 1; letter-spacing: 0.05em; }
  .label-red .label-variety { color: var(--red-word); }
  .label-rose .label-variety { color: var(--rose-word); }
  .label-white .label-variety { color: var(--white-word); }
  .hill { fill: var(--gold); }
</style>
</head>
<body>
<main class="board">
  <svg class="defs" aria-hidden="true">
    <defs>
      <linearGradient id="grain-red" x1="0" y1="0" x2="1" y2="1">
        <stop offset="0" stop-color="#fdfbfa"/><stop offset="0.5" stop-color="#f8f1ef"/><stop offset="1" stop-color="#fcf8f7"/>
      </linearGradient>
      <radialGradient id="grain-rose" cx="0.45" cy="0.45" r="0.7">
        <stop offset="0" stop-color="#fdf6f5"/><stop offset="0.5" stop-color="#f9ebe9"/><stop offset="1" stop-color="#fdf8f7"/>
      </radialGradient>
      <linearGradient id="grain-white" x1="0" y1="0" x2="1" y2="1">
        <stop offset="0" stop-color="#fbfbfb"/><stop offset="0.5" stop-color="#f1f1f3"/><stop offset="1" stop-color="#fafafa"/>
      </linearGradient>
      <linearGradient id="treeline-tone" x1="0" y1="0" x2="0" y2="1">
        <stop offset="0" stop-color="#7c6b3a" stop-opacity="0.25"/><stop offset="0.6" stop-color="#7c6b3a" stop-opacity="0.8"/><stop offset="1" stop-color="#7c6b3a"/>
      </linearGradient>
    </defs>
  </svg>

  <section class="identity">
    <div class="wordmark">
      <div class="wordmark-dot"></div>
      <h1 class="wordmark-name"><span>Quailbrook</span><span>Vineyards</span></h1>
    </div>
    <div class="divider"></div>

    <div class="bottle bottle-red" role="img" aria-label="Dark red wine bottle with gold capsule">
      <div class="label label-red">
        <svg class="label-art" viewBox="0 0 222 222" preserveAspectRatio="none">
          <rect width="222" height="222" fill="url(#grain-red)" role="img" aria-label="Pale wood grain texture"/>
          <path d="M0,200 L0,184 Q111,128 222,178 L222,204 Z" fill="url(#treeline-tone)" role="img" aria-label="Pine tree line silhouette with birds"/>
          <path class="hill" d="M0,196 C60,182 150,186 222,196 L222,210 C160,218 80,204 0,222 Z"/>
        </svg>
        <div class="label-lockup"><div class="label-lockup-dot"></div><div class="label-lockup-name"><span>Quailbrook</span><span>Vineyards</span></div></div>
        <div class="label-variety">Red</div>
      </div>
    </div>
    <div class="bottle bottle-rose" role="img" aria-label="Rosé wine bottle with white capsule">
      <div class="label label-rose">
        <svg class="label-art" viewBox="0 0 222 222" preserveAspectRatio="none">
          <rect width="222" height="222" fill="url(#grain-rose)" role="img" aria-label="Soft pink tree ring texture"/>
          <path d="M0,200 L0,184 Q111,128 222,178 L222,204 Z" fill="url(#treeline-tone)" role="img" aria-label="Pine tree line silhouette with birds"/>
          <path class="hill" d="M0,196 C60,182 150,186 222,196 L222,210 C160,218 80,204 0,222 Z"/>
        </svg>
        <div class="label-lockup"><div class="label-lockup-dot"></div><div class="label-lockup-name"><span>Quailbrook</span><span>Vineyards</span></div></div>
        <div class="label-variety">Rose</div>
      </div>
    </div>
    <div class="bottle bottle-white" role="img" aria-label="Pink tinted wine bottle with white capsule">
      <div class="label label-white">
        <svg class="label-art" viewBox="0 0 222 222" preserveAspectRatio="none">
          <rect width="222" height="222" fill="url(#grain-white)" role="img" aria-label="Light grey wood grain texture"/>
          <path d="M0,200 L0,184 Q111,128 222,178 L222,204 Z" fill="url(#treeline-tone)" role="img" aria-label="Pine tree line silhouette with birds"/>
          <path class="hill" d="M0,196 C60,182 150,186 222,196 L222,210 C160,218 80,204 0,222 Z"/>
        </svg>
        <div class="label-lockup"><div class="label-lockup-dot"></div><div class="label-lockup-name"><span>Quailbrook</span><span>Vineyards</span></div></div>
        <div class="label-variety">White</div>
      </div>
    </div>
  </section>

  <section class="label-panel">
    <div class="label label-red" role="group" aria-label="Wood grain label, red">
      <svg class="label-art" viewBox="0 0 222 222" preserveAspectRatio="none">
        <rect width="222" height="222" fill="url(#grain-red)" role="img" aria-label="Pale wood grain texture"/>
        <path d="M0,200 L0,184 Q111,128 222,178 L222,204 Z" fill="url(#treeline-tone)" role="img" aria-label="Pine tree line silhouette with birds"/>
        <path class="hill" d="M0,196 C60,182 150,186 222,196 L222,210 C160,218 80,204 0,222 Z"/>
      </svg>
      <div class="label-lockup"><div class="label-lockup-dot"></div><div class="label-lockup-name"><span>Quailbrook</span><span>Vineyards</span></div></div>
      <div class="label-variety">Red</div>
    </div>
    <div class="label label-rose" role="group" aria-label="Tree ring label, rose">
      <svg class="label-art" viewBox="0 0 222 222" preserveAspectRatio="none">
        <rect width="222" height="222" fill="url(#grain-rose)" role="img" aria-label="Soft pink tree ring texture"/>
        <path d="M0,200 L0,184 Q111,128 222,178 L222,204 Z" fill="url(#treeline-tone)" role="img" aria-label="Pine tree line silhouette with birds"/>
        <path class="hill" d="M0,196 C60,182 150,186 222,196 L222,210 C160,218 80,204 0,222 Z"/>
      </svg>
      <div class="label-lockup"><div class="label-lockup-dot"></div><div class="label-lockup-name"><span>Quailbrook</span><span>Vineyards</span></div></div>
      <div class="label-variety">Rose</div>
    </div>
    <div class="label label-white" role="group" aria-label="Wood grain label, white">
      <svg class="label-art" viewBox="0 0 222 222" preserveAspectRatio="none">
        <rect width="222" height="222" fill="url(#grain-white)" role="img" aria-label="Light grey wood grain texture"/>
        <path d="M0,200 L0,184 Q111,128 222,178 L222,204 Z" fill="url(#treeline-tone)" role="img" aria-label="Pine tree line silhouette with birds"/>
        <path class="hill" d="M0,196 C60,182 150,186 222,196 L222,210 C160,218 80,204 0,222 Z"/>
      </svg>
      <div class="label-lockup"><div class="label-lockup-dot"></div><div class="label-lockup-name"><span>Quailbrook</span><span>Vineyards</span></div></div>
      <div class="label-variety">White</div>
    </div>
  </section>
</main>
</body>
</html>
```